Harvest Gateway Fellowship Ministries needs a fresh new web design

We are an up and coming multicultural church that aims to bring people into a life changing encounter with God. We need a fresh and inviting website in order to increase our internet presence and make us easier to connect with.
Here are some of the basic requirements for the site:
• Clearly displayed address, service times, and contact info
• A staff profile page
• An area for a calendar with upcoming events and their details
• Social media buttons
• Group pages for the different ministries (youth, children’s church, men, etc…)
• An area for donations and eCommerce
• A resources page for assorted media (podcasts, sermons, videos, etc.…)
• An area for prayer requests.

```html
<!DOCTYPE html>
<html lang="en">
<head>
<meta charset="utf-8">
<title>Harvest Gateway Fellowship Ministries</title>
<link rel="stylesheet" href="https://fonts.googleapis.com/css2?family=Montserrat:wght@400;500;600&family=Open+Sans:ital,wght@0,400;0,600;0,700;1,600&display=swap">
<style>
:root{
  --brown:#7b6a50;
  --blue:#0c2fa2;
  --blue-dark:#0a2788;
  --gold:#e8c81a;
  --gold-text:#f1d24a;
  --text:#555;
  --heading:#111;
  --grey-box:#b3b3b3;
  --crowd:#dcdcdc;
  --white:#fff;
}
*{margin:0;padding:0;box-sizing:border-box}
html,body{width:1200px;height:2338px;overflow:hidden;background:var(--white)}
body{position:relative;font-family:"Open Sans",Arial,sans-serif;color:var(--text)}
.abs{position:absolute}
.top-band{left:0;top:0;width:1200px;height:84px;background:var(--brown);color:var(--white);
  font:500 25px/84px "Montserrat",sans-serif;text-align:center;letter-spacing:.3px}
.header{left:0;top:84px;width:1200px;height:212px;
  background:linear-gradient(180deg,#c9dbe9 0%,#eef3f7 45%,#dfe9f1 100%)}
.brand{left:420px;top:20px;width:360px;text-align:center}
.brand-mark{width:90px;height:90px;border-radius:50%;background:#e9b526;margin:0 auto 14px}
.brand-name{font:600 19px/1.3 "Montserrat",sans-serif;color:var(--blue-dark)}
.contact{right:112px;top:40px;text-align:left;font:14px "Open Sans",sans-serif;color:var(--blue)}
.contact div{display:flex;align-items:center;gap:12px;margin-bottom:12px;justify-content:flex-end}
.socials{right:120px;top:112px;display:flex;gap:7px}
.socials span{width:28px;height:28px;background:var(--blue)}
.nav{left:0;top:296px;width:1200px;height:62px;background:var(--blue);display:flex;align-items:center;
  padding-left:195px;gap:0}
.nav a{color:var(--white);text-decoration:none;font:500 16px "Montserrat",sans-serif;margin-right:70px}
.slider{left:0;top:358px;width:1200px;height:468px;
  background:linear-gradient(100deg,#c08a3c 0%,#e2b466 30%,#b9a88f 55%,#e7c49a 80%,#f3d9b5 100%)}
.arrow{top:155px}
.caption{left:0;top:374px;width:1200px;height:94px;background:rgba(60,45,30,.72);color:var(--white);
  padding:12px 148px;font:500 15px/1.9 "Montserrat",sans-serif}
.caption .ref{position:absolute;right:253px;bottom:8px;color:var(--gold-text);font-size:15px}
.welcome{left:160px;top:860px;width:880px;text-align:center}
.welcome h1{font:500 24px "Montserrat",sans-serif;color:var(--heading);margin-bottom:12px}
.welcome p{font:15.5px/28px "Open Sans",sans-serif;margin-bottom:28px}
.section-title{font:500 22px "Montserrat",sans-serif;color:var(--heading)}
.service-card{left:121px;width:460px;height:140px}
.service-card .photo{position:absolute;left:0;top:0;width:175px;height:140px}
.service-card h3{position:absolute;left:194px;top:0;font:500 17px "Montserrat",sans-serif;color:var(--heading)}
.service-card p{position:absolute;left:194px;top:28px;width:270px;font:13.5px/21px "Open Sans",sans-serif;color:#666}
.btn{background:var(--blue);color:var(--white);font:600 12px "Open Sans",sans-serif;border-radius:3px;
  display:flex;align-items:center;justify-content:center;text-transform:uppercase}
.field{border:1px solid #ccc;background:var(--white);font:13px "Open Sans",sans-serif;color:#333;
  padding:0 14px;display:flex;align-items:center;justify-content:space-between}
.field .req{color:#e02020}
.editor{left:626px;top:1298px;width:367px;height:148px;border:1px solid #ccc}
.editor .label{padding:12px 16px;font:13px "Open Sans",sans-serif;color:#333}
.editor .toolbar{position:absolute;bottom:0;left:0;right:0;height:22px;background:#eee;
  border-top:1px solid #ddd;display:flex;gap:8px;align-items:center;padding-left:84px;font:700 11px Arial,sans-serif;color:#333}
.motto{left:730px;top:1480px;font:italic 600 13px "Open Sans",sans-serif;color:var(--blue)}
.event-band{left:120px;top:1578px;width:960px;height:115px;background:var(--blue)}
.event-tab{left:573px;top:1547px;width:242px;height:42px;background:var(--gold);color:var(--blue);
  font:500 15px/42px "Montserrat",sans-serif;text-align:center}
.event-icon{left:128px;top:1578px;width:106px;height:100px;background:#b5662a;border-radius:6px}
.event-label{left:270px;top:1622px;color:var(--white);font:500 18px "Montserrat",sans-serif}
.count{top:1618px;height:42px;background:var(--white);color:var(--blue);font:500 18px/42px "Montserrat",sans-serif;text-align:center}
.crowd{left:0;top:1800px;width:1200px;height:428px;
  background:linear-gradient(180deg,rgba(220,220,220,0) 0%,var(--crowd) 55%,#e8e8e8 100%)}
.update{left:121px;width:472px;height:90px}
.update .date{position:absolute;left:0;top:0;width:94px;height:90px;background:var(--grey-box);color:var(--white);
  text-align:center;font-family:"Montserrat",sans-serif}
.update .date b{display:block;font-weight:500;font-size:17px;padding-top:10px}
.update .date strong{display:block;font-weight:500;font-size:40px;line-height:46px}
.update p{position:absolute;left:108px;top:0;width:364px;font:11.5px/17px Arial,sans-serif;color:#333}
.update .stamp{position:absolute;left:108px;top:62px;font:700 11px "Open Sans",sans-serif;color:var(--blue)}
.update .more{position:absolute;right:0;top:62px;width:74px;height:26px;border:1px solid var(--blue);border-radius:3px;
  font:12px "Open Sans",sans-serif;color:var(--blue);background:var(--white);display:flex;align-items:center;justify-content:center}
.service-time{left:229px;top:2040px;width:291px;height:157px;background:var(--grey-box);padding:20px 22px;color:#555}
.service-time h4{text-align:center;font:500 16px "Montserrat",sans-serif;color:#555;margin-bottom:14px}
.service-time p{font:15px/29px "Open Sans",sans-serif}
.rings{left:232px;top:2026px;display:flex;gap:13px}
.rings span{width:6px;height:20px;border:1.5px solid #888;border-radius:3px;background:#eee}
.donate-box{left:618px;top:1768px;width:462px;height:141px;background:var(--blue);border-radius:4px;
  padding:18px 14px;color:var(--gold-text);font:12.5px/21px "Open Sans",sans-serif}
.verse-ref{left:622px;top:1930px;font:700 19px "Open Sans",sans-serif;color:var(--blue-dark)}
.verse{left:622px;top:1960px;width:460px;font:italic 600 13px/20px "Open Sans",sans-serif;color:var(--blue)}
.tax{left:724px;top:2064px;font:700 12px "Open Sans",sans-serif;color:#111}
.pay-btn{left:811px;top:2102px;width:86px;height:24px;border-radius:12px;background:#f7c24a;color:#17325c;
  font:700 13px/24px "Open Sans",sans-serif;text-align:center}
.cards{left:778px;top:2148px;display:flex;gap:3px}
.cards span{width:30px;height:19px;border:1px solid #aaa}
.footer{left:0;top:2228px;width:1200px;height:110px;background:var(--brown);color:var(--white);text-align:center;
  font:600 13px "Open Sans",sans-serif;padding-top:26px}
.footer p{margin-bottom:14px}
.footer .code{position:absolute;right:54px;top:45px;font-weight:400}
</style>
</head>
<body>

<div class="abs top-band">"NO LIMITS, NO BOUNDARIES, BUT INCREASE IN JESUS NAME"</div>

<header class="abs header">
  <div class="abs brand">
    <div class="brand-mark"></div>
    <div class="brand-name">Harvest Gateway Fellowship Ministries</div>
  </div>
  <div class="abs contact">
    <div>
      <svg width="16" height="16" viewBox="0 0 24 24"><path d="M6.6 10.8a15 15 0 0 0 6.6 6.6l2.2-2.2c.3-.3.7-.4 1-.2 1.1.4 2.3.6 3.6.6.6 0 1 .4 1 1V20c0 .6-.4 1-1 1A17 17 0 0 1 3 4c0-.6.4-1 1-1h3.5c.6 0 1 .4 1 1 0 1.3.2 2.5.6 3.6.1.3 0 .7-.2 1z" fill="none" stroke="#0c2fa2" stroke-width="2"/></svg>
      <span>555.014.2280</span>
    </div>
    <div>
      <svg width="18" height="13" viewBox="0 0 18 13"><rect x="1" y="1" width="16" height="11" fill="none" stroke="#0c2fa2" stroke-width="1.4"/><path d="M1 1l8 6 8-6" fill="none" stroke="#0c2fa2" stroke-width="1.4"/></svg>
      <span>info@harvestgateway.org</span>
    </div>
  </div>
  <div class="abs socials"><span></span><span></span><span></span><span></span><span></span></div>
</header>

<nav class="abs nav">
  <a href="#">HOME</a><a href="#">ABOUT US</a><a href="#">EVENTS</a><a href="#">PRAYER REQUEST</a><a href="#">DONATE</a><a href="#">CONTACT US</a>
</nav>

<section class="abs slider" role="img" aria-label="Warm golden photo of a hand holding a Holy Bible">
  <svg class="abs arrow" style="left:58px" width="48" height="48" viewBox="0 0 48 48"><circle cx="24" cy="24" r="21" fill="rgba(255,255,255,.25)" stroke="#555" stroke-width="3"/><path d="M28 14L18 24l10 10" fill="none" stroke="#555" stroke-width="3"/></svg>
  <svg class="abs arrow" style="left:1097px" width="48" height="48" viewBox="0 0 48 48"><circle cx="24" cy="24" r="21" fill="rgba(255,255,255,.25)" stroke="#555" stroke-width="3"/><path d="M20 14l10 10-10 10" fill="none" stroke="#555" stroke-width="3"/></svg>
  <div class="abs caption">
    <div>RANDOM BIBLE VERSE</div>
    <div>FOR THE WAGES OF SIN IS DEATH, BUT THE GIFT OF GOD IS ETERNAL LIFE IN CHRIST JESUS OUR LORD</div>
    <span class="ref">ROMANS 6:23</span>
  </div>
</section>

<section class="abs welcome">
  <h1>WELCOME TO HGFM</h1>
  <p>Welcome to Harvest Gateway Fellowship Ministries, a place where we can come together and fellowship. HGFM is located in Cedar Falls, Ohio and we would love to have you worship with us. We believe God is doing something extraordinary through our church and would like for you to be a part. Please prayerfully consider our church as a place you would like to worship and fellowship with us as we continue to grow.</p>
  <p>As you venture on our website please feel free to contact us through email, phone, or leave a prayer request for us to pray on your behalf. Please take a minute and look at our upcoming events.</p>
</section>

<h2 class="abs section-title" style="left:121px;top:1132px">Our service</h2>
<article class="abs service-card" style="top:1196px">
  <div class="photo" role="img" aria-label="Photo of a child praying" style="background:linear-gradient(135deg,#8a6a55,#d9c2ae)"></div>
  <h3>Our Vision</h3>
  <p>At Harvest Gateway Fellowship Ministries we believe in uniting people from various Christian denominations, did for us.</p>
  <div class="abs btn" style="left:200px;top:100px;width:101px;height:32px">Read more</div>
</article>
<article class="abs service-card" style="top:1382px">
  <div class="photo" role="img" aria-label="Photo of people raising hands before a cross at sunset" style="background:linear-gradient(180deg,#e2b27a,#5a3520)"></div>
  <h3>What We Belive</h3>
  <p>At Harvest Gateway Fellowship Ministries we believe in uniting people from various Christian denominations, did for us.</p>
  <div class="abs btn" style="left:191px;top:104px;width:101px;height:32px">Read more</div>
</article>

<h2 class="abs section-title" style="left:626px;top:1124px;letter-spacing:-.5px">Submit a Prayer Request</h2>
<div class="abs field" style="left:626px;top:1169px;width:180px;height:43px">Your Name:<span class="req">*</span></div>
<div class="abs field" style="left:824px;top:1169px;width:169px;height:43px">Your Email Address:<span class="req">*</span></div>
<div class="abs field" style="left:626px;top:1236px;width:180px;height:41px">Prayer Title:<span class="req">*</span></div>
<div class="abs field" style="left:824px;top:1236px;width:169px;height:41px">Prayer Topic:<svg width="10" height="7"><path d="M0 0h10L5 7z" fill="#555"/></svg></div>
<div class="abs editor">
  <div class="label">Your Name:</div>
  <div class="toolbar"><span>B</span><span><i>I</i></span><span><u>U</u></span><span>S</span><span>↶</span><span>↷</span><span>≡</span><span>☰</span></div>
</div>
<div class="abs btn" style="left:627px;top:1471px;width:84px;height:33px;font-weight:400;font-size:13px">Submit</div>
<div class="abs motto">"No limits, No Boundaries, but increase in Jesus name"</div>

<div class="abs event-band"></div>
<div class="abs event-icon" role="img" aria-label="Calendar page illustration"></div>
<div class="abs event-tab">MEMBERSHIP MEETING</div>
<svg class="abs" style="left:684px;top:1588px" width="20" height="11"><path d="M0 0h20L10 11z" fill="#e8c81a"/></svg>
<div class="abs event-label">UPCOMING EVENT :</div>
<div class="abs count" style="left:459px;width:103px">1027 DAYS</div>
<div class="abs count" style="left:584px;width:78px">9 HRS</div>
<div class="abs count" style="left:675px;width:83px">53 MIN</div>
<div class="abs count" style="left:780px;width:86px">55 SEC</div>
<svg class="abs" style="left:972px;top:1612px" width="22" height="56"><path d="M2 2l18 26L2 54" fill="none" stroke="#fff" stroke-width="2"/></svg>

<div class="abs crowd" role="img" aria-label="Faint grey silhouettes of a worshipping crowd with raised hands"></div>

<h2 class="abs section-title" style="left:121px;top:1727px;font-size:18px">OUR LATEST UPDATES</h2>
<article class="abs update" style="top:1776px">
  <div class="date"><b>JUN</b><strong>07</strong></div>
  <p>Our food pantry team gathered last week to pack meals for local families, and more helpers are welcome to join next month.</p>
  <span class="stamp">JUN 13 2014</span>
  <span class="more">MORE</span>
</article>
<article class="abs update" style="top:1901px">
  <div class="date"><b>JUN</b><strong>09</strong></div>
  <p>The youth choir will lead worship this Sunday evening, so bring friends and family for a night of praise and prayer.</p>
  <span class="stamp">JUN 10 2014</span>
  <span class="more">MORE</span>
</article>

<div class="abs service-time">
  <h4>SERVICE TIME</h4>
  <p>MON &nbsp;to FRI &nbsp;( eve 7.00 pm)</p>
  <p>SAT &nbsp;&nbsp;( eve 7.00 pm )</p>
  <p>SUN ( mor 8 am &nbsp;&nbsp;&nbsp;eve 6 pm)</p>
</div>
<div class="abs rings"><span></span><span></span><span></span><span></span><span></span><span></span><span></span><span></span><span></span><span></span><span></span><span></span><span></span><span></span><span></span><span></span></div>

<h2 class="abs section-title" style="left:618px;top:1727px;font-size:18px">DONATE</h2>
<div class="abs donate-box">Making a gift to Harvest Gateway Fellowship Ministries will support us with our community outreach events such as our annual "Back to School" event and our Thanksgiving basket local as well as the international community. We appreciate your support in helping us build God's kingdom. Help us Help All. God bless you!</div>
<div class="abs verse-ref">Matthew 25: 40</div>
<div class="abs verse">"The King will reply, 'Truly I tell you, whatever you did for one of the least of these brothers and sisters of mine,<br>you did for me."</div>
<div class="abs tax">ALL DONATIONS ARE TAX REFUNDABLE</div>
<div class="abs pay-btn">Donate</div>
<div class="abs cards"><span></span><span></span><span></span><span></span><span></span></div>

<footer class="abs footer">
  <p>Privacy Policy &nbsp;|&nbsp; Terms Conditions &nbsp;|&nbsp; Sitemap &nbsp;|&nbsp; Contact Us</p>
  <p>© 2012 HGFM. All Rights Reserved</p>
  <span class="code">D4</span>
</footer>

</body>
</html>
```